Consulting company business cards

We have a base design, but would be willing to update. We have a new logo/"tag" that needs to be added. Current business card design is attached for reference into our "style."

Industry/Entity Type

Business

Contact Information for Business Card

Should contain name and title, office number, mobile number if appropriate, e-mail, website, physical address, and company logo.

Font styles to use
Other font styles liked:
• See current card design on KorvandBCard

Colors
0455a3
85acd3
aaaaaa

Requirements
Must have
• Our colors are navy blue, gray, and a lighter blue
Nice to have
• Design that I can easily drop in new names/titles as we hire employees.

```html
<!DOCTYPE html>
<html lang="en">
<head>
<meta charset="utf-8">
<title>Harlow Business Cards</title>
<link href="https://fonts.googleapis.com/css2?family=Open+Sans:wght@400;600;700&display=swap" rel="stylesheet">
<style>
  :root {
    --backdrop: #9a9896;
    --navy: #03304f;
    --navy-band: #0a3554;
    --navy-soft: #0c3a5b;
    --light-blue: #7fb0d3;
    --gray-text: #4f4f4f;
    --tag-gray: #7a7a7a;
    --rule: #9a9a9a;
    --paper: #ffffff;
  }
  * { margin: 0; padding: 0; box-sizing: border-box; }
  html, body { width: 1200px; height: 750px; overflow: hidden; }
  body {
    background: var(--backdrop);
    font-family: "Open Sans", sans-serif;
    position: relative;
  }
  .card {
    position: absolute;
    top: 228px;
    width: 462px;
    height: 262px;
    border-radius: 12px;
    overflow: hidden;
  }
  /* Front */
  .card-front { left: 124px; background: var(--paper); }
  .front-watermark {
    position: absolute;
    left: 236px; top: 4px;
    width: 226px; height: 240px;
    background: radial-gradient(closest-side, #eef3f7 0%, #f5f8fa 60%, rgba(255,255,255,0) 100%);
  }
  .brand { position: absolute; left: 30px; top: 34px; }
  .brand-name {
    display: flex; align-items: center; gap: 7px;
    font-weight: 700; font-size: 38px; line-height: 1;
    color: var(--navy); letter-spacing: 0;
  }
  .brand-dot {
    width: 30px; height: 30px; border-radius: 50%;
    background: var(--light-blue);
  }
  .brand-tag {
    margin-top: 6px;
    font-size: 9.5px; letter-spacing: 2px;
    color: var(--tag-gray);
  }
  .person { position: absolute; right: 28px; top: 117px; text-align: right; }
  .person-name { font-weight: 600; font-size: 17px; color: var(--navy); line-height: 1.1; }
  .person-title { font-size: 13.5px; color: var(--light-blue); line-height: 1.35; }
  .divider {
    position: absolute; left: 28px; top: 149px;
    width: 302px; height: 1px; background: var(--rule);
  }
  .contacts { position: absolute; left: 24px; top: 160px; list-style: none; }
  .contacts li {
    display: flex; align-items: center; gap: 7px;
    height: 17.7px;
    font-size: 12.5px; color: var(--gray-text);
  }
  .contacts svg { width: 12px; height: 12px; fill: var(--navy); flex: none; }
  .address {
    position: absolute; right: 28px; top: 195px;
    text-align: right; font-size: 12.5px; line-height: 17.7px;
    color: var(--gray-text);
  }
  .front-band {
    position: absolute; left: 0; bottom: 0;
    width: 100%; height: 18px; background: var(--navy-band);
  }
  /* Back */
  .card-back { left: 618px; background: var(--navy); }
  .back-watermark {
    position: absolute; left: 4px; top: 8px;
    width: 250px; height: 250px;
    background: radial-gradient(closest-side, var(--navy-soft) 0%, #0a3758 60%, rgba(3,48,79,0) 100%);
  }
  .back-brand {
    position: absolute; right: 24px; top: 156px;
    text-align: right; color: var(--paper);
  }
  .back-name { font-weight: 700; font-size: 46px; line-height: 1; letter-spacing: 0; }
  .back-tag { margin-top: 8px; font-size: 9.5px; letter-spacing: 1.6px; font-weight: 600; }
  .back-url { margin-top: 4px; font-size: 13px; letter-spacing: 3px; }
</style>
</head>
<body>
  <section class="card card-front">
    <div class="front-watermark" role="img" aria-label="Faint brand emblem watermark"></div>
    <div class="brand">
      <div class="brand-name">HARLOW<span class="brand-dot"></span></div>
      <div class="brand-tag">A CLOUD CONSULTING COMPANY</div>
    </div>
    <div class="person">
      <div class="person-name">Marenkorvand</div>
      <div class="person-title">Office Manager</div>
    </div>
    <div class="divider"></div>
    <ul class="contacts">
      <li><svg viewBox="0 0 24 24"><path d="M6.6 10.8a15.1 15.1 0 0 0 6.6 6.6l2.2-2.2c.3-.3.7-.4 1-.2 1.1.4 2.3.6 3.6.6.6 0 1 .4 1 1V20c0 .6-.4 1-1 1A17 17 0 0 1 3 4c0-.6.4-1 1-1h3.5c.6 0 1 .4 1 1 0 1.3.2 2.5.6 3.6.1.3 0 .7-.2 1z"/></svg>555.240.1836</li>
      <li><svg viewBox="0 0 24 24"><path d="M6 3h12v5H6zM3 9h18v8h-3v4H6v-4H3zm5 6v4h8v-4z"/></svg>555.240.1879</li>
      <li><svg viewBox="0 0 24 24"><path d="M2 5h20v14H2zm2 2v.5l8 5 8-5V7l-8 5z"/></svg>mkorvand@harlowtech.com</li>
      <li><svg viewBox="0 0 24 24"><path d="M12 2a10 10 0 1 0 0 20 10 10 0 0 0 0-20zm-1 17.9A8 8 0 0 1 4.1 10L9 15v1a2 2 0 0 0 2 2zm6.9-2.5A2 2 0 0 0 16 16h-1v-3a1 1 0 0 0-1-1H8v-2h2a1 1 0 0 0 1-1V7h2a2 2 0 0 0 2-2v-.4a8 8 0 0 1 2.9 12.8z"/></svg>www.harlowtech.com</li>
    </ul>
    <div class="address">1185 N Alder Row<br>Westbrook Indiana 46000</div>
    <div class="front-band"></div>
  </section>

  <section class="card card-back">
    <div class="back-watermark" role="img" aria-label="Large tonal brand emblem"></div>
    <div class="back-brand">
      <div class="back-name">HARLOW</div>
      <div class="back-tag">A CLOUD CONSULTING COMPANY</div>
      <div class="back-url">www.harlowtech.com</div>
    </div>
  </section>
</body>
</html>
```